K & R Acre Works. Business card design

We need a business card designed for a new business. We have a bulldozer and tractor service. We clear land and make wildlife food plots. We provide disking, bush hogging, and site prep services.
I have attached an image of a business card that I like and would like my business cards to look similar.

Target Market(s)

anyone needing bulldozer and/or tractor services

Industry/Entity Type

Business

Contact Information for Business Card

K & R Acre Works, Operated by 7-T-Ranch
Wade Colton
601-472-3358
wcr4817@fieldmail-example.com

Font styles to use
Sans Serif

Colors

Designer to choose colors to be used in the design.

Requirements
Must have
• image of tractor and bulldozer
• Land Clearing
• Wildlife food plots
• Bush Hogging
• Disking
• Site prep
Nice to have
• i have included a image of a business card that i like. I would like mine to be similar.

```html
<!DOCTYPE html>
<html lang="en">
<head>
<meta charset="utf-8">
<title>K &amp; R Acre Works – Business Card</title>
<link href="https://fonts.googleapis.com/css2?family=Bebas+Neue&family=Roboto:wght@400&display=swap" rel="stylesheet">
<style>
  :root {
    --page-bg: #1c1c1c;
    --card-bg: #ffffff;
    --ink: #2f2f2f;
    --ink-soft: #3a3a3a;
    --sky: #9fc3de;
    --foliage: #5f8a3c;
    --foliage-dark: #3f5f2a;
    --soil: #8a6f4e;
  }
  * { margin: 0; padding: 0; box-sizing: border-box; }
  html, body {
    width: 1200px; height: 897px; overflow: hidden;
    background: var(--page-bg);
  }
  .card {
    position: absolute; left: 40px; top: 129px;
    width: 1120px; height: 639px;
    background: var(--card-bg);
    display: flex;
  }
  .card-info {
    width: 561px; height: 100%;
    position: relative;
    color: var(--ink);
    font-family: 'Roboto', sans-serif;
  }
  .company-name {
    position: absolute; left: 40px; top: 40px;
    font-family: 'Bebas Neue', sans-serif;
    font-weight: 400;
    font-size: 52px; line-height: 54px;
    letter-spacing: 0.5px;
    color: var(--ink-soft);
    text-transform: uppercase;
  }
  .contact-name {
    position: absolute; left: 41px; top: 230px;
    font-size: 37px; letter-spacing: 0.5px;
    text-transform: uppercase;
  }
  .contact-line {
    position: absolute; left: 42px;
    font-size: 33px;
  }
  .contact-phone { top: 301px; }
  .contact-email { top: 347px; font-size: 31px; }
  .service-list {
    position: absolute; left: 42px; top: 418px;
    list-style: none;
    font-size: 33px; line-height: 45px;
  }
  .service-list li { display: flex; align-items: center; }
  .service-list li::before {
    content: ""; width: 13px; height: 13px; border-radius: 50%;
    background: var(--ink); margin: 0 33px 0 5px;
  }
  .card-photo {
    flex: 1; height: 100%;
    background: linear-gradient(180deg, var(--sky) 0%, var(--foliage) 14%, var(--foliage-dark) 45%, #6d7a3f 68%, var(--soil) 85%, #6f8a45 100%);
  }
</style>
</head>
<body>
  <div class="card">
    <div class="card-info">
      <h1 class="company-name">K &amp; R Acre Works<br>Operated by 7-T-Ranch</h1>
      <p class="contact-name">Wade Colton</p>
      <p class="contact-line contact-phone">P : 601-472-3358</p>
      <p class="contact-line contact-email">E : wcr4817@fieldmail-example.com</p>
      <ul class="service-list">
        <li>Land Clearing</li>
        <li>Wildlife food plots</li>
        <li>Bush Hogging</li>
        <li>Disking | Site prep</li>
      </ul>
    </div>
    <div class="card-photo" role="img" aria-label="Photo of a yellow bulldozer with its blade lowered on a cleared dirt site, green trees behind"></div>
  </div>
</body>
</html>
```